Logo and Card design for KRV Home Solutions LLC

I need an edgier logo and business card designs. Current logo attached. I like the colors below. I would like the logo to incorporate a home in the design.
Title = Principal-Acquisitions
Email:KRVHOMESOLUTIONS@fernmail.example
555-214-0937
facebook
IG
2 sided business card with the front being contact info a slogan about selling a home fast. The back incorporating What we do. Buy houses, land, or commercial property as is. We find solutions to make the process of selling simple and fair.

Target Market(s)

Motivated house sellers.

Industry/Entity Type

Business

Contact Information for Business Card

Who we are: We are a Faith based Real Estate Investment Company. We pay cash for homes in any condition and can close quick. Whatever the reason you need to sell fast, we can help. We believe in creating win-win solutions to help you in your time of need. We care! We can help!

Logo Text

KRV Home Solutions LLC

Font styles to use
Sans Serif

Colors
33a6d7
0355a3
85abd2
cee9f5
9d9d9d
b2b2b2
ffffff

Requirements
Must have
• Old logo attached. I want something edgier.
• Company name, phone number, description on the back of what we can do. Pay all cash. Buy in as is condition. No fees,Commisions or closing costs.Close quick. No hassles with solutions to meet your unique situation.
• Call today for an offer within 24 hours.

```html
<!DOCTYPE html>
<html lang="en">
<head>
<meta charset="utf-8">
<title>KRV Home Solutions – Business Card</title>
<link href="https://fonts.googleapis.com/css2?family=Jost:wght@400&family=Work+Sans:wght@400;600&display=swap" rel="stylesheet">
<style>
  :root {
    --navy: #243a73;
    --grey: #5f5f63;
    --grey-light: #9d9d9d;
    --text: #55565b;
    --white: #ffffff;
    --backdrop: #e9e9e9;
    --accent: #c14b7a;
  }
  * { box-sizing: border-box; margin: 0; padding: 0; }
  html, body { width: 1200px; height: 1130px; overflow: hidden; }
  body { background: var(--backdrop); font-family: "Work Sans", sans-serif; position: relative; }

  .card {
    position: absolute; left: 250px; width: 700px; height: 400px;
    overflow: hidden; box-shadow: 0 4px 14px rgba(0,0,0,.18);
  }
  .card--front { top: 125px; background: var(--white); }
  .card--back { top: 585px; background: var(--navy); color: var(--white); }

  .wordmark {
    position: absolute; display: flex; align-items: center; gap: 10px;
    font-family: "Jost", sans-serif; font-weight: 400; white-space: nowrap;
  }
  .wordmark__dot { border-radius: 50%; flex: none; }
  .card--front .wordmark { left: 62px; top: 186px; font-size: 21px; color: var(--navy); }
  .card--front .wordmark__dot { width: 12px; height: 12px; background: var(--navy); }
  .card--back .wordmark { left: 0; right: 0; justify-content: center; top: 160px; font-size: 32px; color: var(--white); }
  .card--back .wordmark__dot { width: 16px; height: 16px; background: var(--white); }

  .divider { position: absolute; left: 306px; top: 100px; width: 2px; height: 160px; background: var(--grey); }

  .details { position: absolute; left: 342px; top: 96px; }
  .details__name { font-family: "Jost", sans-serif; font-weight: 400; font-size: 27px; color: var(--navy); letter-spacing: .3px; }
  .details__title { font-size: 15px; color: var(--text); margin-top: 1px; }
  .details__rule { width: 38px; height: 2px; background: var(--grey-light); margin: 10px 0 24px; }

  .contact { list-style: none; }
  .contact li { display: flex; align-items: center; gap: 12px; font-size: 15px; color: var(--text); line-height: 20px; }
  .contact svg { width: 13px; height: 13px; flex: none; }
  .contact__dot { width: 12px; height: 12px; border-radius: 50%; background: var(--navy); flex: none; }
  .contact__dot--accent { background: var(--accent); }

  .tagline {
    position: absolute; left: 0; right: 0; top: 304px; text-align: center;
    font-size: 14px; font-weight: 600; letter-spacing: 2px; color: #3c3d42;
  }
  .wave { position: absolute; left: 0; bottom: 0; width: 700px; height: 80px; }

  .about {
    position: absolute; left: 0; right: 0; top: 282px; text-align: center;
    font-size: 15px; line-height: 21px; color: #e7ebf5;
  }
</style>
</head>
<body>
  <section class="card card--front">
    <div class="wordmark"><span class="wordmark__dot"></span><span>KRV Home Solutions</span></div>
    <div class="divider"></div>
    <div class="details">
      <h1 class="details__name">KRV HOME SOLUTIONS</h1>
      <p class="details__title">Principal-Acquisitions</p>
      <div class="details__rule"></div>
      <ul class="contact">
        <li>
          <svg viewBox="0 0 24 24"><circle cx="12" cy="12" r="12" fill="#243a73"/><path d="M8 6.5l2 .2 1 3-1.4 1.1a7 7 0 0 0 3.6 3.6l1.1-1.4 3 1 .2 2c-.3 1-1.4 1.6-2.5 1.4A10 10 0 0 1 6.6 9c-.2-1.1.4-2.2 1.4-2.5z" fill="#fff"/></svg>
          555-214-0937
        </li>
        <li><span class="contact__dot"></span>/krvcashoffers</li>
        <li><span class="contact__dot contact__dot--accent"></span>@krv.cashoffers</li>
        <li>
          <svg viewBox="0 0 24 24"><circle cx="12" cy="12" r="12" fill="#243a73"/><rect x="6" y="8" width="12" height="8" fill="none" stroke="#fff" stroke-width="1.6"/><path d="M6 8l6 4.5L18 8" fill="none" stroke="#fff" stroke-width="1.6"/></svg>
          KRVHOMESOLUTIONS@fernmail.example
        </li>
      </ul>
    </div>
    <p class="tagline">SELLING A HOME FAST</p>
    <svg class="wave" viewBox="0 0 700 80" preserveAspectRatio="none">
      <path d="M0 40 C 180 10, 420 12, 700 58 L700 80 L0 80 Z" fill="var(--grey)"/>
      <path d="M0 50 C 200 22, 430 28, 700 62 L700 80 L0 80 Z" fill="var(--white)"/>
      <path d="M0 56 C 220 34, 460 48, 700 66 L700 80 L0 80 Z" fill="var(--navy)"/>
    </svg>
  </section>

  <section class="card card--back">
    <div class="wordmark"><span class="wordmark__dot"></span><span>KRV Home Solutions</span></div>
    <p class="about">
      Pay all cash. Buy in as is condition. No fees,Commisions<br>
      or closing costs.Close quick. No hassles with solutions<br>
      to meet your unique situation.<br>
      Call today for an offer within 24 hours.
    </p>
  </section>
</body>
</html>
```